Halvery Construction Group Website

Need a dynamic corporate website that can be built on with time. We want to get our information out to the world and have a place where customers can submit requests for proposals.

Target Market(s)

Custom home owners and buyers. Architects and Real Estate Agents.

Industry/Entity Type

Construction

Number of Pages Required

3 page

Font styles to use
Serif
Sans Serif

Requirements
Must have
• Company logo, about, company contact information, biography, contact, projects,
• Sleek, modern, clean, attractive design.
• Online form customers can use for filling out a request for project proposal.
• Linkedin hyperlink.
• Uses www.halveryconstructiongroup.example

```html
<!DOCTYPE html>
<html lang="en">
<head>
<meta charset="utf-8">
<title>Halvery Construction Group</title>
<link href="https://fonts.googleapis.com/css2?family=Raleway:wght@400;500;600&family=Open+Sans:wght@400;600&display=swap" rel="stylesheet">
<style>
:root{
  --brand-blue:#1a4fa0;
  --navy:#0b2a7a;
  --nav-active:#3d8fd1;
  --text-dark:#1d1d1d;
  --text-body:#555;
  --text-muted:#777;
  --footer-bg:#f3f3f3;
  --field-bg:#ffffff;
  --send-top:#4a98d8;
  --send-bottom:#2f7cc0;
}
*{box-sizing:border-box;margin:0;padding:0}
html,body{width:1143px;height:1200px;overflow:hidden;background:#fff}
body{position:relative;font-family:"Raleway",sans-serif;color:var(--text-dark)}
.abs{position:absolute}

/* hero */
.hero{left:0;top:0;width:1143px;height:504px;
  background:
    radial-gradient(ellipse 260px 300px at 270px 330px,#6f86b3 0%,rgba(111,134,179,0) 70%),
    radial-gradient(ellipse 380px 190px at 800px 420px,#5d7eb4 0%,rgba(93,126,180,0) 75%),
    linear-gradient(180deg,#f4f7fb 0%,#e6edf5 45%,#c5d1e0 100%);}
.logo{left:94px;top:22px;display:flex;align-items:center;gap:9px}
.logo-mark{width:34px;height:34px;background:var(--brand-blue)}
.logo-name{font-family:"Raleway",sans-serif;font-weight:600;font-size:17px;color:var(--brand-blue);line-height:1.1;letter-spacing:.5px}
.nav{left:0;top:33px;width:1143px;height:23px}
.nav a{position:absolute;top:0;height:23px;line-height:23px;font-size:14px;color:var(--text-dark);text-decoration:none;transform:translateX(-50%);white-space:nowrap}
.nav a.active{background:var(--nav-active);color:#fff;width:71px;text-align:center}
.caption{left:98px;top:427px;height:31px;padding:0 6px 0 5px;background:rgba(255,255,255,.85);font-size:19.5px;line-height:31px;font-weight:500;color:#111}
.dots{left:537px;top:486px;display:flex;gap:3px}
.dots span{width:21px;height:3px;background:#fff;border-radius:2px}
.dots span.on{background:var(--nav-active)}

/* content */
.section-title{font-size:19.5px;font-weight:500;color:var(--text-dark)}
.bio-title{left:95px;top:540px}
.bio-text{left:94px;top:585px;width:436px;font-size:11.6px;line-height:17.1px;letter-spacing:-.25px;color:var(--text-body)}
.btn-read{left:94px;top:727px;width:107px;height:29px;background:var(--navy);color:#fff;font-size:12px;line-height:29px;text-align:center;text-decoration:none}
.projects-title{left:601px;top:540px}
.project-img{top:589px;width:210px;height:156px}
.project-cap{top:752px;font-size:15px;color:#333}

/* footer */
.footer{left:0;top:847px;width:1143px;height:353px;background:var(--footer-bg)}
.f-head{top:884px;font-size:11.5px;letter-spacing:.6px;color:#333}
.f-about{left:94px;top:928px;width:255px;font-size:11.5px;line-height:18px;color:var(--text-muted)}
.f-more{left:94px;top:1035px;font-size:11.5px;color:var(--text-muted);text-decoration:none}
.f-links a{position:absolute;left:385px;font-size:11.5px;color:var(--text-muted);text-decoration:none}
.contact-line{left:571px;font-family:"Open Sans",sans-serif;font-size:10.5px;color:#666;display:flex;gap:10px;letter-spacing:.3px;line-height:18px}
.contact-line svg{flex:none;margin-top:2px}
.socials{left:576px;top:1077px;display:flex;gap:19px}
.socials a{width:14px;height:14px;border-radius:50%;background:#8a8a8a;display:block}
.field{left:830px;width:218px;background:var(--field-bg);font-family:"Open Sans",sans-serif;font-size:8.5px;color:#666;padding:9px 8px}
.btn-send{left:928px;top:1075px;width:120px;height:27px;background:linear-gradient(var(--send-top),var(--send-bottom));color:#fff;font-family:"Open Sans",sans-serif;font-size:9px;letter-spacing:.5px;line-height:27px;text-align:center;border:none}
.copyright{left:0;top:1158px;width:1143px;text-align:center;font-family:"Open Sans",sans-serif;font-size:10.5px;color:#777}
</style>
</head>
<body>

<div class="abs hero" role="img" aria-label="Smiling construction workers in hard hats and plaid shirts at a building site"></div>

<div class="abs logo">
  <span class="logo-mark"></span>
  <span class="logo-name">HALVERY<br>CONSTRUCTION GROUP</span>
</div>

<nav class="abs nav">
  <a class="active" href="#" style="left:700px">Home</a>
  <a href="#" style="left:776px">About</a>
  <a href="#" style="left:844px">Bio</a>
  <a href="#" style="left:918px">Projects</a>
  <a href="#" style="left:1015px">Contact us</a>
</nav>

<div class="abs caption">Lorem ipsum dolor sit amet, consectetur adipiscing elit</div>
<div class="abs dots"><span class="on"></span><span></span><span></span></div>

<h2 class="abs section-title bio-title">Our Bio</h2>
<p class="abs bio-text">Lorem ipsum dolor sit amet, consectetur adipiscing elit. Proin aliquet dui eget nisi mattis, et blandit lacus lobortis. In hac habitasse platea dictumst. Nulla ligula erat, accumsan ut consequat a, finibus vitae sapien. Suspendisse dapibus volutpat justo, finibus luctus augue finibus et. Pellentesque habitant morbi tristique senectus et netus et malesuada fames ac turpis egestas. Proin at tristique est. Cras vulputate ut felis et auctor. Sed ornare ligula non enim efficitur vehicula. Proin non nibh magna. Aliquam vel lorem sagittis tortor scelerisque</p>
<a class="abs btn-read" href="#">Read More</a>

<h2 class="abs section-title projects-title">Our Projects</h2>
<div class="abs project-img" style="left:605px;background:linear-gradient(180deg,#4f8fe0 0%,#8fbdf0 45%,#b9a98a 75%,#6d6050 100%)" role="img" aria-label="Tower cranes above a multi-storey concrete building under construction"></div>
<div class="abs project-cap" style="left:606px">Lorem ipsum dolor</div>
<div class="abs project-img" style="left:838px;background:linear-gradient(180deg,#8a8f98 0%,#c9c4bb 40%,#a9865e 70%,#5a4a3e 100%)" role="img" aria-label="Timber frame house under construction beside a brick wall"></div>
<div class="abs project-cap" style="left:839px">Contatgnry Popilar</div>

<footer class="abs footer"></footer>
<div class="abs f-head" style="left:94px">ABOUT</div>
<div class="abs f-head" style="left:385px">LINKS</div>
<div class="abs f-head" style="left:571px">CONTACT INFO</div>
<div class="abs f-head" style="left:830px">CONTACT US</div>

<p class="abs f-about">Lorem ipsum dolor sit amet, consectetur adipi-scing elit. Nulla sodales, odio id dapibus pulvi-nar, augue risus efficitur ipsum, at venenatis dolor dui et leo. Praesent vulputate quis erat quis finibus.</p>
<a class="abs f-more" href="#">Read More &gt;&gt;</a>

<div class="f-links">
  <a href="#" style="top:928px">Privacy Policy</a>
  <a href="#" style="top:957px">Terms and Conditions</a>
  <a href="#" style="top:987px">Site Map</a>
  <a href="#" style="top:1016px">Affiliates &amp; Vendors</a>
  <a href="#" style="top:1045px">Contact Us</a>
</div>

<div class="abs contact-line" style="top:927px">
  <svg width="14" height="11" viewBox="0 0 14 11"><rect x=".75" y=".75" width="12.5" height="9.5" fill="none" stroke="#777" stroke-width="1.3"/><path d="M1 1.5 7 6l6-4.5" fill="none" stroke="#777" stroke-width="1.3"/></svg>
  <span>hello@halveryconstruction.example</span>
</div>
<div class="abs contact-line" style="top:967px">
  <svg width="11" height="11" viewBox="0 0 11 11"><path d="M2 .5 4 3 3 4.5c.7 1.5 2 2.8 3.5 3.5L8 7l2.5 2-1 1.5C5 10.5.5 6 .5 1.5z" fill="#777"/></svg>
  <span>(800) 555-0147</span>
</div>
<div class="abs contact-line" style="top:1017px">
  <svg width="9" height="12" viewBox="0 0 9 12"><path d="M4.5 0A4.5 4.5 0 0 0 0 4.5C0 8 4.5 12 4.5 12S9 8 9 4.5A4.5 4.5 0 0 0 4.5 0zm0 6.2a1.7 1.7 0 1 1 0-3.4 1.7 1.7 0 0 1 0 3.4z" fill="#777"/></svg>
  <span>412 Larkmoor Avenue, Suite 210<br>Fernbrook, FL 33990</span>
</div>

<div class="abs socials">
  <a href="#" aria-label="Social link 1"></a>
  <a href="#" aria-label="Professional profile"></a>
  <a href="#" aria-label="Social link 3"></a>
  <a href="#" aria-label="Social link 4"></a>
  <a href="#" aria-label="Social link 5"></a>
  <a href="#" aria-label="Social link 6"></a>
</div>

<div class="abs field" style="top:931px;height:28px">Name</div>
<div class="abs field" style="top:962px;height:28px">Email Address</div>
<div class="abs field" style="top:995px;height:63px">Message</div>
<button class="abs btn-send">SEND</button>

<div class="abs copyright">Copyright © 2016 - halveryconstructiongroup.example, All Rights Reserved</div>

</body>
</html>
```